Tellmora Corporate Stationery

Look for design of all new corporate stationery for an existing insurance broking business that is going through a redesign and move from older partners to younger family members. New Logo is attached. Company is Brisbane based.
Colours in the Logo is Hex #43bed8 and website features a lot of hex #17b8d8. Website front page "A plan to protect you" - headline. "Professional and Individual advice to protect your greatest assets" - tagline.

Stationery required: Business Cards, Letter head, Thank-you cards, Birthday cards, Presentation folders, With Compliment slips and a powerpoint template. We also would like to send a card to all customers with the something along of the lines of "something new".

Target Market(s)

Customers of Insurance business looking at superannuation, life and income protection insurance, investment advice and wills

Industry/Entity Type

Insurance Broker

Font styles to use
Other font styles liked:
• same as logo

Requirements
Must have
• The above designs for new stationery for the new business including:
• Business Cards, Letter head, Thank-you cards, Birthday cards, Presentation folders, With Compliment slips and a powerpoint template. We also would like to send a card to all customers with the something along of the lines of "something new".
Nice to have
• It is a new look - long time family business being passed to next generation - big focus on advice for YOU, individual advice etc..

```html
<!DOCTYPE html>
<html lang="en">
<head>
<meta charset="utf-8">
<title>Tellmora Financial Group – Business Card</title>
<link rel="stylesheet" href="https://fonts.googleapis.com/css2?family=Exo+2:wght@300;400;500&display=swap">
<style>
  :root {
    --brand-cyan: #43bed8;
    --ink-grey: #707174;
    --icon-grey: #7c7d80;
    --panel-grey: #ebebeb;
    --line-grey: #e2e2e2;
    --card-white: #ffffff;
    --page-white: #ffffff;
  }
  * { box-sizing: border-box; margin: 0; padding: 0; }
  html, body {
    width: 1200px; height: 1000px; overflow: hidden;
    background: var(--page-white);
    font-family: "Exo 2", sans-serif;
  }
  .canvas { position: relative; width: 1200px; height: 1000px; }
  .card {
    position: absolute; left: 206px; width: 787px; height: 486px;
    background: var(--card-white);
    box-shadow: 0 0 6px rgba(0,0,0,0.12);
    overflow: hidden;
  }
  .card-front { top: 0; }
  .card-back { top: 514px; }

  .front-pattern {
    position: absolute; inset: 0;
    background: radial-gradient(circle at 50% 60%, #f7f7f7 0%, #ededed 55%, #f4f4f4 100%);
  }
  .wordmark-panel {
    position: absolute; left: 124px; top: 262px; width: 544px; height: 130px;
    background: var(--card-white);
    border: 6px solid #e9e9e9;
    border-radius: 12px;
    text-align: center;
    color: var(--brand-cyan);
    font-weight: 500;
    white-space: nowrap;
  }
  .wordmark-name { font-size: 74px; letter-spacing: 10px; line-height: 76px; margin-top: 4px; text-transform: uppercase; }
  .wordmark-sub { font-size: 36px; letter-spacing: 3px; line-height: 38px; text-transform: uppercase; }
  .mark-circle {
    position: absolute; left: 308px; top: 108px; width: 170px; height: 170px;
    border-radius: 50%;
    border: 16px solid var(--brand-cyan);
    background: var(--card-white);
  }

  .back-lines { position: absolute; inset: 0; }
  .name-panel {
    position: absolute; left: 180px; top: 62px; width: 410px; height: 114px;
    background: var(--panel-grey);
    border: 4px solid #dedede;
    border-radius: 50px 0 0 50px;
    padding: 8px 0 0 82px;
    color: var(--brand-cyan);
    white-space: nowrap;
  }
  .person-name { font-size: 60px; font-weight: 400; letter-spacing: 1px; line-height: 60px; }
  .person-role { font-size: 29px; font-weight: 300; letter-spacing: 1.5px; line-height: 32px; }
  .back-circle {
    position: absolute; left: 584px; top: 40px; width: 172px; height: 172px;
    border-radius: 50%;
    border: 13px solid var(--brand-cyan);
    background: var(--card-white);
  }
  .contact-list { list-style: none; }
  .contact-row {
    position: absolute; left: 190px; width: 562px; height: 40px;
    background: var(--panel-grey);
    border-radius: 20px;
    display: flex; align-items: center; justify-content: flex-end;
    padding-right: 112px;
    color: var(--ink-grey);
    font-size: 25px; letter-spacing: 1px;
    white-space: nowrap;
  }
  .contact-icon { position: absolute; left: 470px; top: -4px; width: 54px; height: 46px; }
</style>
</head>
<body>
<main class="canvas">

  <section class="card card-front" aria-label="Business card front">
    <div class="front-pattern" role="img" aria-label="Decorative background of concentric arcs and diagonal line bands in light grey"></div>
    <div class="mark-circle"></div>
    <div class="wordmark-panel">
      <div class="wordmark-name">Tellmora</div>
      <div class="wordmark-sub">Financial Group</div>
    </div>
  </section>

  <section class="card card-back" aria-label="Business card back">
    <svg class="back-lines" width="787" height="486" viewBox="0 0 787 486" aria-hidden="true">
      <g fill="none" stroke="var(--line-grey)" stroke-width="3">
        <path d="M180 118 H31 V421 H190"/>
        <path d="M44 118 V362 H190"/>
        <path d="M56 118 V302 H190"/>
        <path d="M69 118 V243 H190"/>
        <path d="M100 230 H190 M100 256 H190"/>
        <path d="M100 290 H190 M100 314 H190"/>
        <path d="M100 350 H190 M100 374 H190"/>
        <path d="M100 409 H190 M100 433 H190"/>
      </g>
    </svg>

    <div class="name-panel">
      <div class="person-name">John Doe</div>
      <div class="person-role">Financial Advisor</div>
    </div>
    <div class="back-circle"></div>

    <ul class="contact-list">
      <li class="contact-row" style="top:223px">48 Quayside Row, Brisbane
        <svg class="contact-icon" viewBox="0 0 54 46" aria-hidden="true">
          <path d="M4 22 L27 4 L50 22" fill="none" stroke="var(--icon-grey)" stroke-width="4"/>
          <path d="M11 22 V44 H22 V32 H32 V44 H43 V22 L27 10 Z" fill="var(--icon-grey)"/>
        </svg>
      </li>
      <li class="contact-row" style="top:283px">(07) 5550 1842
        <svg class="contact-icon" viewBox="0 0 54 46" aria-hidden="true">
          <path d="M22 3 H29 V13 H26 V33 H29 V43 H22 Q17 23 22 3 Z" fill="var(--icon-grey)"/>
        </svg>
      </li>
      <li class="contact-row" style="top:342px">contact@tellmorafinancesite.com
        <svg class="contact-icon" viewBox="0 0 54 46" aria-hidden="true">
          <rect x="3" y="7" width="48" height="32" fill="var(--icon-grey)"/>
          <path d="M3 7 L27 27 L51 7 M3 39 L21 22 M51 39 L33 22" fill="none" stroke="#ffffff" stroke-width="2.5"/>
        </svg>
      </li>
      <li class="contact-row" style="top:402px">www.tellmorafinancesite.com
        <svg class="contact-icon" viewBox="0 0 54 46" aria-hidden="true">
          <circle cx="27" cy="23" r="21" fill="#ffffff" stroke="#d0d0d0" stroke-width="3"/>
          <circle cx="27" cy="23" r="16" fill="none" stroke="var(--icon-grey)" stroke-width="3"/>
          <path d="M11 23 H43 M27 7 V39 M27 7 Q17 23 27 39 M27 7 Q37 23 27 39" fill="none" stroke="var(--icon-grey)" stroke-width="2"/>
        </svg>
      </li>
    </ul>
  </section>

</main>
</body>
</html>
```